Waterjet manufacturing company needs brochure design

We need a brochure that outlines why waterjet manufacturing is beneficial for a variety of industries, our capabilities, core competencies and competitive advantages (see attached documents). The design should include our logo and include the same colours. (Dark blue RGB – 2,86,162, Light Blue RGB – 0,146,201). The design should be very clean, professional and eye catching. I've attached a few photos that can be used. Regarding the photo of the robot, please make the background white.

Target Market(s)

Manufacturing, construction, aerospace, home building

Colors

Designer to choose colors to be used in the design.

Requirements
Must have
• - exact Logo colours included in design (see description)
• - booklet style design (not tri-fold)
• - professional looking
• - Logo on front cover with writing underneath:
• High Quality
• Tight Tolerance
• Components
• - Pinwheel, Worklane, Reelhive and Glossora icons in Contact Us section

```html
<!DOCTYPE html>
<html lang="en">
<head>
<meta charset="utf-8">
<title>Northbay Waterjet Brochure</title>
<link rel="stylesheet" href="https://fonts.googleapis.com/css2?family=Montserrat:wght@300;400;600;700&family=Open+Sans:ital,wght@0,400;0,600;1,400&display=swap">
<style>
:root{
  --navy:#0256a2;
  --sky:#0092c9;
  --ink:#2a3440;
  --muted:#6b7682;
  --paper:#f4f6f8;
  --white:#ffffff;
  --photo-dark:#1f2c44;
  --photo-mid:#5d6f86;
  --photo-light:#c9d2dc;
  --bg-1:#34507a;
  --bg-2:#9ea1b5;
  --bg-3:#3f5f87;
  --bg-4:#9a9db2;
}
*{box-sizing:border-box;margin:0;padding:0}
html,body{width:1200px;height:2921px;overflow:hidden}
body{font-family:"Open Sans",Arial,sans-serif;color:var(--ink)}
.scene{height:730px;display:flex;align-items:center;justify-content:center}
.scene--cover{background:var(--bg-1)}
.scene--outer{background:var(--bg-2)}
.scene--compare{background:var(--bg-3)}
.scene--materials{background:var(--bg-4);height:731px}

/* ---------- cover ---------- */
.cover{position:relative;background:var(--white);overflow:hidden;font-family:"Montserrat",Arial,sans-serif;box-shadow:0 6px 18px rgba(0,0,0,.25)}
.cover--solo{width:820px;height:575px;font-size:16px}
.cover--page{width:540px;height:380px;font-size:10.5px}
.cover-head{position:absolute;left:0;top:0;right:0;height:15%;display:flex;align-items:center;padding:0 4%;background:var(--paper)}
.brand{display:flex;align-items:center;gap:.5em;width:30%}
.brand-mark{width:1.2em;height:1.2em;background:var(--navy);flex:0 0 auto}
.brand-name{font-weight:700;color:var(--navy);font-size:1.05em;text-transform:uppercase;letter-spacing:.02em}
.cover-contact{width:40%;text-align:center}
.cover-contact h3{color:var(--navy);font-weight:700;font-size:1.25em}
.cover-contact p{font-family:"Open Sans",Arial,sans-serif;font-size:.62em;color:var(--ink);line-height:1.35}
.cover-address{width:30%;text-align:right;font-style:normal;font-family:"Open Sans",Arial,sans-serif;font-size:.62em;line-height:1.35;color:var(--ink)}
.cover-tagline{position:absolute;left:0;right:0;top:15%;height:9%;background:var(--navy);color:var(--white);display:flex;align-items:center;padding:0 4%;font-weight:300;font-size:1.2em;white-space:nowrap}
.cover-tagline b{font-weight:700;margin-left:.3em}
.cover-photo{position:absolute;left:0;right:0;top:24%;bottom:8%;background:linear-gradient(120deg,var(--photo-light) 0%,var(--photo-mid) 40%,var(--photo-dark) 100%)}
.cover-title{position:absolute;right:5%;top:31%;color:var(--white);text-align:left;line-height:1.05}
.cover-title strong{display:block;font-weight:700;font-size:2.6em;letter-spacing:.02em}
.cover-title span{display:block;font-weight:300;font-size:2.05em;letter-spacing:.03em}
.cover-foot{position:absolute;left:0;right:0;bottom:0;height:8%;background:var(--white);border-top:.25em solid var(--photo-light)}
.site-tab{position:absolute;left:4%;top:-.25em;height:100%;display:flex;align-items:center;padding:0 1.6em;background:#dfe4ea;border-radius:0 0 1em 1em;font-family:"Open Sans",Arial,sans-serif;font-size:.7em;color:var(--muted)}
.site-tab b{color:var(--ink);font-weight:600}

/* ---------- spreads ---------- */
.spread{position:relative;display:flex;width:1080px;height:380px;box-shadow:0 6px 18px rgba(0,0,0,.25)}
.page{position:relative;width:540px;height:380px;background:var(--white);overflow:hidden}
.page--left::after{content:"";position:absolute;top:0;right:0;width:14px;height:100%;background:linear-gradient(90deg,rgba(0,0,0,0),rgba(0,0,0,.08))}
.page--right::before{content:"";position:absolute;top:0;left:0;width:14px;height:100%;background:linear-gradient(270deg,rgba(0,0,0,0),rgba(0,0,0,.08));z-index:2}
.page-foot{position:absolute;left:0;right:0;bottom:0;height:22px;border-top:3px solid var(--photo-light)}
.page-foot .site-tab{font-size:7.5px;left:24px;padding:0 14px;top:-3px;border-radius:0 0 10px 10px}

/* back cover */
.back{background:var(--navy);color:var(--white);display:flex;flex-direction:column;align-items:center;justify-content:center;font-family:"Montserrat",Arial,sans-serif;gap:10px}
.back .brand{width:auto;justify-content:center}
.back .brand-mark{background:var(--white);width:14px;height:14px}
.back .brand-name{color:var(--white);font-size:14px}
.back-line{display:flex;flex-direction:column;align-items:center;gap:4px;font-family:"Open Sans",Arial,sans-serif;font-size:8px;text-align:center;line-height:1.35}
.back-line svg{width:12px;height:12px}
.socials{display:flex;gap:22px;margin-top:14px;list-style:none}
.socials li{display:flex;align-items:center;gap:5px;font-size:8px;font-family:"Open Sans",Arial,sans-serif}
.socials li::before{content:"";width:9px;height:9px;border:1px solid var(--white)}

/* comparison table */
.compare{padding:22px 20px 0 24px;border-left:6px solid var(--navy)}
.compare h2{font-family:"Montserrat",Arial,sans-serif;font-weight:300;color:var(--navy);font-size:19px;margin-bottom:8px}
.compare h2 b{font-weight:700}
.compare table{width:100%;border-collapse:collapse;font-size:7.2px;text-align:center}
.compare th{background:var(--navy);color:var(--white);font-family:"Montserrat",Arial,sans-serif;font-weight:600;font-size:8.5px;padding:6px 3px;letter-spacing:.04em}
.compare th:first-child{background:#1d3e70}
.compare td{padding:5px 3px;border-bottom:1px solid #e3e7ec;color:var(--muted);line-height:1.3}
.compare td:first-child{color:var(--ink);text-align:left;padding-left:6px}
.compare td.is-waterjet{color:var(--sky);font-style:italic;font-weight:600;background:#f1f7fb}
.compare tr.rating td{border-bottom:none;font-family:"Montserrat",Arial,sans-serif;font-weight:600;font-size:11px;color:var(--ink);padding-top:8px}
.compare tr.rating td.is-waterjet{color:var(--sky);font-style:normal}
.score::before{content:"";display:inline-block;width:8px;height:8px;background:currentColor;margin-right:4px;vertical-align:0}

/* why choose */
.why-band{height:44px;background:var(--navy);color:var(--white);display:flex;align-items:center;padding:0 28px;font-family:"Montserrat",Arial,sans-serif;font-size:17px;font-weight:300}
.why-band b{font-weight:700;margin-left:5px}
.why-body{display:flex;padding:12px 18px 0 28px;gap:14px}
.why-text{width:60%}
.why-text h3{font-family:"Montserrat",Arial,sans-serif;font-weight:300;color:var(--navy);font-size:13px;margin-bottom:8px}
.why-text h3 b{font-weight:700}
.why-text p{font-size:7px;line-height:1.45;margin-bottom:6px}
.why-photo{width:40%;height:170px;margin-top:10px;background:radial-gradient(circle at 55% 45%,#6b88b0 0%,#b9cde2 45%,#ffffff 80%)}
.why-contact{display:flex;gap:30px;padding:10px 28px 0;align-items:flex-start}
.why-contact .ghost{font-family:"Montserrat",Arial,sans-serif;font-weight:700;color:#c9d0d8;font-size:13px;text-transform:uppercase;width:120px}
.why-contact h4{font-family:"Montserrat",Arial,sans-serif;color:var(--navy);font-size:12px;font-weight:600}
.why-contact p,.why-contact address{font-size:7px;line-height:1.4;font-style:normal}
.why-contact address{font-weight:600;margin-top:14px}

/* benefits & materials */
.spread--materials{overflow:hidden}
.benefits{padding:24px 0 0 28px;width:63%}
.benefits h2{font-family:"Montserrat",Arial,sans-serif;color:var(--navy);font-weight:300;font-size:17px;line-height:1.1;margin-bottom:10px}
.benefits h2 b{display:block;font-weight:700;font-size:19px}
.benefits dl{font-size:6.8px;line-height:1.3}
.benefits dt{color:var(--navy);font-weight:600;font-size:7.4px;margin-top:4px}
.benefits dd{color:var(--muted)}
.feature-photo{position:absolute;top:0;bottom:0;left:360px;width:380px;background:linear-gradient(160deg,#9db0c6 0%,#5b7391 50%,#c4ced9 100%)}
.feature-label{position:absolute;left:390px;top:120px;color:var(--white);font-family:"Montserrat",Arial,sans-serif;line-height:1.05;z-index:3}
.feature-label small{font-size:9px;display:block}
.feature-label strong{font-size:22px;font-weight:600;display:block}
.feature-label em{font-size:8px;font-style:normal;display:block;margin-top:4px}
.materials-arch{position:absolute;left:590px;top:0;width:200px;height:380px;background:var(--white);border-radius:100% 0 0 100% / 50% 0 0 50%;z-index:2}
.materials-title{position:absolute;left:612px;top:150px;font-family:"Montserrat",Arial,sans-serif;color:var(--navy);z-index:3;line-height:1.05}
.materials-title span{display:block;font-weight:300;font-size:22px}
.materials-title strong{display:block;font-weight:700;font-size:24px}
.materials-list{position:absolute;left:210px;right:22px;top:24px;list-style:none;z-index:3}
.materials-list li{display:flex;gap:10px;margin-bottom:9px}
.materials-list li::before{content:"";flex:0 0 12px;height:12px;border:1.5px solid var(--navy);margin-top:2px}
.materials-list b{display:block;font-family:"Montserrat",Arial,sans-serif;color:var(--navy);font-size:7.4px;text-transform:uppercase}
.materials-list p{font-size:6.8px;line-height:1.35;color:var(--muted)}
.spread--materials .page-foot{z-index:4}
</style>
</head>
<body>

<section class="scene scene--cover">
  <article class="cover cover--solo">
    <header class="cover-head">
      <div class="brand"><span class="brand-mark"></span><span class="brand-name">Northbay Waterjet</span></div>
      <div class="cover-contact"><h3>Contact us</h3><p>(555) 014-2290<br>info@northbay-waterjet.example</p></div>
      <address class="cover-address">48 Larkfield Rd Unit 9<br>Brookmere, ON<br>K0A 1X0</address>
    </header>
    <div class="cover-tagline">In a faster forward world, innovation doesn't wait for <b>technology</b></div>
    <div class="cover-photo" role="img" aria-label="Waterjet cutting head spraying water over a metal plate"></div>
    <h1 class="cover-title"><strong>High quality</strong><span>Tight Tolerance</span><span>Components</span></h1>
    <footer class="cover-foot"><span class="site-tab">www.<b>northbay-waterjet</b>.example</span></footer>
  </article>
</section>

<section class="scene scene--outer">
  <div class="spread">
    <div class="page page--left back">
      <div class="brand"><span class="brand-mark"></span><span class="brand-name">Northbay Waterjet</span></div>
      <div class="back-line">
        <svg viewBox="0 0 12 12" fill="none" stroke="#fff" stroke-width="1"><path d="M6 11s4-4.2 4-6.8A4 4 0 0 0 2 4.2C2 6.8 6 11 6 11z"/><circle cx="6" cy="4.3" r="1.4"/></svg>
        <span>48 Larkfield Rd Unit 9<br>Brookmere, ON<br>K0A 1X0</span>
      </div>
      <div class="back-line">
        <svg viewBox="0 0 12 12" fill="none" stroke="#fff" stroke-width="1"><path d="M3 1.5h2l1 2.5-1.3 1a6 6 0 0 0 2.3 2.3l1-1.3 2.5 1v2a1 1 0 0 1-1 1A8.5 8.5 0 0 1 2 2.5a1 1 0 0 1 1-1z"/></svg>
        <span>(555) 014-2290</span>
      </div>
      <div class="back-line">
        <svg viewBox="0 0 12 12" fill="none" stroke="#fff" stroke-width="1"><rect x="1" y="2.5" width="10" height="7"/><path d="M1 2.5l5 4 5-4"/></svg>
        <span>info@northbay-waterjet.example</span>
      </div>
      <ul class="socials"><li>Pinwheel</li><li>Worklane</li><li>Reelhive</li><li>Glossora</li></ul>
    </div>
    <div class="page page--right">
      <article class="cover cover--page">
        <header class="cover-head">
          <div class="brand"><span class="brand-mark"></span><span class="brand-name">Northbay Waterjet</span></div>
          <div class="cover-contact"><h3>Contact us</h3><p>(555) 014-2290<br>info@northbay-waterjet.example</p></div>
          <address class="cover-address">48 Larkfield Rd Unit 9<br>Brookmere, ON<br>K0A 1X0</address>
        </header>
        <div class="cover-tagline">In a faster forward world, innovation doesn't wait for <b>technology</b></div>
        <div class="cover-photo" role="img" aria-label="Waterjet cutting head spraying water over a metal plate"></div>
        <h1 class="cover-title"><strong>High quality</strong><span>Tight Tolerance</span><span>Components</span></h1>
        <footer class="cover-foot"><span class="site-tab">www.<b>northbay-waterjet</b>.example</span></footer>
      </article>
    </div>
  </div>
</section>

<section class="scene scene--compare">
  <div class="spread">
    <div class="page page--left compare">
      <h2>Comparative Cutting <b>Technologies</b></h2>
      <table>
        <thead><tr><th>FACTORS</th><th>WATERJET</th><th>PLASMA</th><th>LASER</th><th>EDM</th></tr></thead>
        <tbody>
          <tr><td>Process</td><td class="is-waterjet">Erosion using high pressure water and garnet</td><td>Burning/melting using a high temperature arc</td><td>Melting using a concentrated laser light beam</td><td>Erosion using an electrical discharge</td></tr>
          <tr><td>Secondary Processing</td><td class="is-waterjet">Usually none. The cold cutting process typically leaves a finished edge product ready for end use</td><td>Typically yes. Slag grinding required for removal of HAZ and flattening to eliminate distortion from heat</td><td>Sometimes yes. Required removal of oxidized edge and HAZ</td><td>Usually none, very minimal HAZ present</td></tr>
          <tr><td>Materials Cut</td><td class="is-waterjet">Virtually any material</td><td>Primarily steel, stainless steel and aluminum</td><td>A variety of materials, but typically steel, stainless steel and aluminum</td><td>Conductive materials only</td></tr>
          <tr><td>Thickness cut</td><td class="is-waterjet">Up to 24"</td><td>Up to 2-3"</td><td>Generally 1" or less</td><td>Generally 12" or less</td></tr>
          <tr><td>Accuracy</td><td class="is-waterjet">Up to 0.001"</td><td>Up to 0.010"</td><td>Up to 0.001"</td><td>Up to 0.0001"</td></tr>
          <tr><td>Machine setup</td><td class="is-waterjet">Same setup for all materials</td><td>Different setup for different jobs</td><td>Different gasses and parameters for different jobs</td><td>Different wire types for different jobs</td></tr>
          <tr class="rating"><td></td><td class="is-waterjet"><span class="score">4.9/5.0</span></td><td><span class="score">4.4/5.0</span></td><td><span class="score">4.2/5.0</span></td><td><span class="score">4.6/5.0</span></td></tr>
        </tbody>
      </table>
      <div class="page-foot"><span class="site-tab">www.<b>northbay-waterjet</b>.example</span></div>
    </div>
    <div class="page page--right">
      <div class="why-band">Why Choose <b>Northbay Waterjet?</b></div>
      <div class="why-body">
        <div class="why-text">
          <h3>A choice that makes <b>the difference</b></h3>
          <p>Located in an industrial core, Northbay Waterjet is an employee owned and operated manufacturing company committed to providing high quality custom precision cutting, on time, every time.</p>
          <p>Our state of the art facility offers leading edge waterjet and laser cutting services, utilizing robotics and multi-directional 5-axis cutting capability to produce precise 3D parts.</p>
          <p>Capable of pumping 100 000 PSI, we run one of the most powerful waterjets in the region, cutting thicker materials faster and with greater precision.</p>
          <p>Our talented operators bring over 35 years of experience, giving faster turnaround, higher throughput and transparent communication on every job.</p>
        </div>
        <div class="why-photo" role="img" aria-label="Robotic cutting tool surrounded by a water splash on a white background"></div>
      </div>
      <div class="why-contact">
        <span class="ghost">Northbay Waterjet</span>
        <div><h4>Contact us</h4><p>(555) 014-2290<br>info@northbay-waterjet.example</p></div>
        <address>(555) 014-2290<br>info@northbay-waterjet.example<br>48 Larkfield Rd Unit 9<br>Brookmere, ON<br>K0A 1X0</address>
      </div>
      <div class="page-foot"><span class="site-tab">www.<b>northbay-waterjet</b>.example</span></div>
    </div>
  </div>
</section>

<section class="scene scene--materials">
  <div class="spread spread--materials">
    <div class="page page--left">
      <div class="benefits">
        <h2>What Northbay Waterjet <b>can do for you</b></h2>
        <dl>
          <dt>Versatility</dt><dd>Can cut any material from 1/16th of an inch to over 20" in high or low volume</dd>
          <dt>Increased Productivity</dt><dd>Elimination of secondary processing increases productivity while maintaining high quality</dd>
          <dt>Speed</dt><dd>Faster than conventional cutting tools for quick turnaround</dd>
          <dt>Precision</dt><dd>Waterjet cutting can make parts to extremely tight tolerances, typically +/- 0.002" and as tight as +/- 0.001"</dd>
          <dt>Simple</dt><dd>Setup and fixturing can be completed in minutes no matter the shape or dimensions</dd>
          <dt>Cold Cutting Process</dt><dd>No heat affected zones, stress or hardening imparted into your cut material</dd>
          <dt>Smooth Edge Finish</dt><dd>No secondary finishing processes necessary unlike other conventional cutting methods</dd>
          <dt>Minimal Kerf</dt><dd>High accuracy and the ability to cut endless materials means unlimited opportunities</dd>
          <dt>Omni-directional Cutting</dt><dd>Allows for complex 3D designs and tight corners</dd>
        </dl>
      </div>
      <div class="page-foot"><span class="site-tab">www.<b>northbay-waterjet</b>.example</span></div>
    </div>
    <div class="page page--right">
      <ul class="materials-list">
        <li><div><b>Metals</b><p>Steel, stainless, aluminum, copper, brass and titanium cut cleanly without heat distortion.</p></div></li>
        <li><div><b>Composites</b><p>Carbon fibre, fibreglass and laminates cut without fraying, delamination or dust.</p></div></li>
        <li><div><b>Stone &amp; Tile</b><p>Granite, marble, porcelain and ceramic cut into intricate inlays and custom shapes.</p></div></li>
        <li><div><b>Glass</b><p>Flat, laminated and tempered-ready glass cut with smooth edges and no cracking.</p></div></li>
        <li><div><b>Plastic, Rubber &amp; Acrylic</b><p>Gaskets, seals and signage cut with no melting or warping of the material.</p></div></li>
        <li><div><b>Wood</b><p>Hardwoods, plywood and MDF cut with no burning, scorching or sawdust.</p></div></li>
        <li><div><b>Cement</b><p>Concrete and cement boards cut for construction and architectural detail work.</p></div></li>
      </ul>
      <div class="page-foot"><span class="site-tab">www.<b>northbay-waterjet</b>.example</span></div>
    </div>
    <div class="feature-photo" role="img" aria-label="Close-up of a waterjet nozzle cutting a metal sheet"></div>
    <div class="materials-arch"></div>
    <div class="feature-label"><small>Benefits of</small><strong>Waterjet<br>Cutting</strong><em>with Northbay Waterjet</em></div>
    <div class="materials-title"><span>Materials</span><strong>We Cut</strong></div>
  </div>
</section>

</body>
</html>
```